Lanternfield Drinks business cards

We need a business card design for our new logo. The company is modern, progressive, professional, yet approachable. The key products are ready to drink bottles and cans of coffee based beverages.
These cards will be a critical part of the first impression made by our sales organization, business development team, and all external facing personnel.
Card can be a vertical or horizontal orientation.

Target Market(s)

Customers, suppliers, business partners

Industry/Entity Type

Business

Contact Information for Business Card

Business cards should feature Company Name and Logo.

Font styles to use
Serif

Colors

Designer to choose colors to be used in the design.

Requirements
Must have
• Strong readability of Name, phone #, mobile number and email address.
• Job title, website url, Street Address, and other details can be secondary level readability.
Nice to have
• High impact, simplistic quality design.
• Ok to utilize the 'H in the box' separate from the company name

```html
<!DOCTYPE html>
<html lang="en">
<head>
<meta charset="utf-8">
<title>Lanternfield Drinks business cards</title>
<link rel="stylesheet" href="https://fonts.googleapis.com/css2?family=Lora:wght@400;700&display=swap">
<style>
  :root {
    --backdrop: #e9e6e1;
    --card-white: #ffffff;
    --card-black: #111111;
    --brand-orange: #f05a2a;
    --brand-amber: #f7941d;
    --text-light: #ffffff;
  }
  * { box-sizing: border-box; margin: 0; padding: 0; }
  html, body { width: 1200px; height: 900px; overflow: hidden; }
  body {
    background: var(--backdrop);
    font-family: "Lora", Georgia, serif;
    position: relative;
  }
  .card {
    position: absolute;
    width: 520px;
    height: 297px;
    border-radius: 3px;
    box-shadow: 0 10px 24px rgba(0,0,0,0.18);
    overflow: hidden;
  }
  /* Front */
  .card-front {
    left: 50px; top: 200px;
    background: var(--card-white);
    display: flex; flex-direction: column;
    align-items: center; justify-content: center; gap: 22px;
  }
  .brand-square {
    width: 84px; height: 84px;
    background: var(--brand-orange);
  }
  .brand-name {
    font-weight: 700;
    font-size: 31px;
    letter-spacing: 0.5px;
    color: var(--brand-orange);
    text-transform: uppercase;
    white-space: nowrap;
  }
  /* Back */
  .card-back {
    left: 630px; top: 400px;
    background: var(--card-black);
  }
  .back-wave { position: absolute; inset: 0; width: 100%; height: 100%; }
  .contact-block {
    position: absolute; left: 40px; top: 30px;
    color: var(--text-light);
  }
  .person-name {
    font-weight: 700; font-size: 19px; line-height: 23px;
    color: var(--brand-orange); letter-spacing: 0.4px;
  }
  .person-title {
    font-size: 12px; line-height: 16px; color: var(--brand-amber);
    letter-spacing: 0.6px; margin-bottom: 11px;
  }
  .contact-list { list-style: none; }
  .contact-list li {
    display: flex; align-items: flex-start; gap: 7px;
    font-size: 13px; line-height: 18px;
  }
  .contact-list li.address { margin-top: 6px; }
  .contact-list svg { width: 11px; height: 11px; margin-top: 3px; flex: none; fill: var(--brand-orange); }
  .back-brand {
    position: absolute; right: 30px; top: 34px;
    display: flex; flex-direction: column; align-items: flex-end; gap: 10px;
  }
  .back-brand .brand-square { width: 72px; height: 72px; }
  .back-brand .brand-name { font-size: 12px; letter-spacing: 0.3px; }
  .back-url {
    position: absolute; right: 26px; bottom: 66px;
    font-size: 11px; color: var(--text-light);
  }
</style>
</head>
<body>

<section class="card card-front">
  <div class="brand-square"></div>
  <div class="brand-name">Lanternfield Drinks</div>
</section>

<section class="card card-back">
  <svg class="back-wave" viewBox="0 0 520 297" preserveAspectRatio="none" aria-hidden="true">
    <path d="M0 262 C160 262 330 220 520 150 L520 297 L0 297 Z" fill="var(--brand-orange)"/>
    <path d="M0 246 C150 248 300 215 440 168 C310 225 160 258 0 260 Z" fill="var(--brand-amber)"/>
  </svg>

  <div class="back-brand">
    <div class="brand-square"></div>
    <div class="brand-name">Lanternfield Drinks</div>
  </div>

  <div class="contact-block">
    <div class="person-name">DANA WHITCOMB</div>
    <div class="person-title">MANAGING DIRECTOR</div>
    <ul class="contact-list">
      <li><svg viewBox="0 0 12 12"><path d="M1 4 Q6 0 11 4 L9 6 L8 4.5 L4 4.5 L3 6 Z M2 7 H10 V11 H2 Z"/></svg>444 555 0182</li>
      <li><svg viewBox="0 0 12 12"><path d="M3 0 H9 V12 H3 Z M4 1.5 V9 H8 V1.5 Z" fill-rule="evenodd"/></svg>888 555 0147</li>
      <li><svg viewBox="0 0 12 12"><path d="M0 2 H12 V10 H0 Z M1 3 L6 7 L11 3" fill-rule="evenodd"/></svg>hello@lanternfielddrinks.com</li>
      <li><svg viewBox="0 0 12 12"><circle cx="6" cy="6" r="6"/></svg>www.lanternfielddrinks.com</li>
      <li class="address"><svg viewBox="0 0 12 12"><path d="M6 0 A4 4 0 0 1 10 4 C10 7 6 12 6 12 C6 12 2 7 2 4 A4 4 0 0 1 6 0 Z M6 2.5 A1.5 1.5 0 1 0 6.01 2.5 Z" fill-rule="evenodd"/></svg><span>421, Address line here,<br>Dummy Code, 45452<br>Country Name</span></li>
    </ul>
  </div>

  <div class="back-url">www.lanternfielddrinks.com</div>
</section>

</body>
</html>
```